BOLD & MINIMALIST DESIGN NEEDED

We want a very bold but minimalistic business card design that is impactful and utilizes both sides of the business card. Our current logo is included for your use.

We want bold fonts and good use of negative space. We don't want the logo to overpower the design.

Target Market(s)

Professionals who are building new commercial buildings.

Industry/Entity Type

Construction

Contact Information for Business Card

Name, Title, email, office phone, cell phone, website

Font styles to use
Serif
Sans Serif

Requirements
Must have
• Bold design!

```html
<!DOCTYPE html>
<html lang="en">
<head>
<meta charset="utf-8">
<title>Kestreline Business Card</title>
<link href="https://fonts.googleapis.com/css2?family=Montserrat:wght@700&family=Roboto:wght@500;700;900&display=swap" rel="stylesheet">
<style>
  :root {
    --bg: #dfe4e2;
    --card: #ffffff;
    --ink: #111111;
    --grey: #555555;
    --green: #7cc242;
  }
  * { margin: 0; padding: 0; box-sizing: border-box; }
  html, body { width: 1200px; height: 716px; overflow: hidden; background: var(--bg); }
  .canvas { position: relative; width: 1200px; height: 716px; }
  .card {
    position: absolute; left: 369px; width: 461px; height: 264px;
    background: var(--card); border-radius: 12px;
  }
  .card--front { top: 94px; }
  .card--back { top: 382px; }
  .brand {
    display: flex; align-items: center; gap: 10px;
    font-family: "Roboto", sans-serif; font-weight: 900; color: var(--ink);
    letter-spacing: 0.5px;
  }
  .brand__mark { background: var(--green); flex: none; }
  .card--front .brand {
    position: absolute; left: 0; right: 0; top: 112px;
    justify-content: center; font-size: 38px;
  }
  .card--front .brand__mark { width: 26px; height: 26px; }
  .card--back .brand {
    position: absolute; left: 19px; top: 60px; font-size: 17px; gap: 6px;
  }
  .card--back .brand__mark { width: 12px; height: 12px; }
  .person {
    position: absolute; right: 16px; top: 128px; text-align: right;
    color: var(--grey);
  }
  .person__name { font-family: "Montserrat", sans-serif; font-weight: 700; font-size: 16px; line-height: 20px; }
  .person__title { font-family: "Roboto", sans-serif; font-weight: 700; font-size: 12px; line-height: 16px; margin-top: 2px; }
  .divider {
    position: absolute; left: 19px; top: 161px; width: 360px; height: 1.5px; background: var(--ink);
  }
  .contact {
    position: absolute; right: 16px; top: 180px; text-align: right; list-style: none;
    font-family: "Roboto", sans-serif; font-weight: 700; font-size: 12.5px; line-height: 16.7px;
    color: var(--grey);
  }
</style>
</head>
<body>
<div class="canvas">
  <section class="card card--front">
    <div class="brand"><span class="brand__mark"></span>KESTRELINE</div>
  </section>
  <section class="card card--back">
    <div class="brand"><span class="brand__mark"></span>KESTRELINE</div>
    <div class="person">
      <p class="person__name">NOURA KETTANI</p>
      <p class="person__title">Designer</p>
    </div>
    <div class="divider"></div>
    <ul class="contact">
      <li>+100-24-86135</li>
      <li>hello@kestreline.com</li>
      <li>www.kestreline.com</li>
      <li>Ridge Lane 14 &nbsp;| R. No. 08 P.O. 2210, BD</li>
    </ul>
  </section>
</div>
</body>
</html>
```